Business Card - Tidal Lanes

Need Business Card design for company named Tidal Lanes. Software development focused mainly on Brindle Orvix & Zelt Apps. I've attached our logo with both a black and white background. Please add trademark symbol to logo when using.

```html
<!DOCTYPE html>
<html lang="en">
<head>
<meta charset="utf-8">
<title>Tidal Lanes – Business Card</title>
<link rel="stylesheet" href="https://fonts.googleapis.com/css2?family=Open+Sans:wght@400;600;700&display=swap">
<style>
  :root {
    --page-bg: #e9e6e1;
    --card-black: #050505;
    --brand-orange: #f39a2b;
    --brand-yellow: #f7c21a;
    --name-orange: #f5a021;
    --divider-gold: #b8860b;
    --text-white: #ffffff;
    --text-soft: #e6e6e6;
  }
  * { margin: 0; padding: 0; box-sizing: border-box; }
  html, body {
    width: 1200px; height: 720px; overflow: hidden;
    background: var(--page-bg);
    font-family: "Open Sans", Arial, sans-serif;
  }
  .canvas {
    position: relative; width: 1200px; height: 720px;
    display: flex; align-items: center; justify-content: center; gap: 40px;
  }
  .card {
    position: relative; width: 540px; height: 309px;
    box-shadow: 0 6px 18px rgba(0,0,0,0.18);
  }
  .card--front { background: var(--card-black); color: var(--text-white); }
  .card--back {
    background: linear-gradient(100deg, var(--brand-yellow) 0%, var(--brand-orange) 100%);
    display: flex; align-items: center; justify-content: center;
  }

  .brand { position: absolute; left: 40px; top: 52px; display: flex; align-items: center; gap: 12px; }
  .brand__dot { width: 30px; height: 30px; border-radius: 50%; background: var(--brand-orange); }
  .brand__name { font-weight: 700; font-size: 30px; letter-spacing: -0.5px; color: var(--text-white); }

  .person { position: absolute; left: 40px; top: 206px; }
  .person__name { font-weight: 700; font-size: 19px; color: var(--name-orange); line-height: 1.2; }
  .person__title { font-size: 14px; color: var(--text-soft); }

  .contact {
    position: absolute; left: 325px; top: 150px;
    padding-left: 12px; border-left: 1px solid var(--divider-gold);
    font-size: 13.5px; color: var(--text-soft); line-height: 1.55;
  }
  .contact__row { display: flex; align-items: center; gap: 8px; }
  .contact__icon { width: 12px; height: 12px; flex: none; }
  .contact__address { margin-top: 10px; font-size: 11.5px; }

  .back-brand { display: flex; align-items: center; gap: 16px; }
  .back-brand__dot { width: 44px; height: 44px; border-radius: 50%; background: var(--text-white); }
  .back-brand__name { font-weight: 700; font-size: 46px; letter-spacing: -1px; color: var(--text-white); }
</style>
</head>
<body>
  <main class="canvas">
    <section class="card card--front" aria-label="Card front">
      <div class="brand">
        <span class="brand__dot"></span>
        <span class="brand__name">Tidal Lanes</span>
      </div>
      <div class="person">
        <p class="person__name">Your Name</p>
        <p class="person__title">Title</p>
      </div>
      <div class="contact">
        <p class="contact__row">
          <svg class="contact__icon" viewBox="0 0 12 12" aria-hidden="true"><rect x="3" y="0.5" width="6" height="11" rx="1.2" fill="none" stroke="#f5a021" stroke-width="1.4"/><circle cx="6" cy="9.3" r="0.8" fill="#f5a021"/></svg>
          555-014-2290
        </p>
        <p class="contact__row">
          <svg class="contact__icon" viewBox="0 0 12 12" aria-hidden="true"><path d="M2.5 4.5 A1 1 0 0 1 3.5 3.5 L8.5 3.5 A1 1 0 0 1 9.5 4.5 L11 8 L1 8 Z" fill="#f5a021"/><rect x="1" y="7.5" width="10" height="2" fill="#f5a021"/><circle cx="3.2" cy="10" r="1" fill="#f5a021"/><circle cx="8.8" cy="10" r="1" fill="#f5a021"/></svg>
          555-017-6431
        </p>
        <p class="contact__address">4120 Harbor Row, Marlow, FL 30021</p>
      </div>
    </section>

    <section class="card card--back" aria-label="Card back">
      <div class="back-brand">
        <span class="back-brand__dot"></span>
        <span class="back-brand__name">Tidal Lanes</span>
      </div>
    </section>
  </main>
</body>
</html>
```